Every Shelf Set Neatly or ESN Organized needs a business card design. ESN Organized is a professi

We need a business card design that is clean, sharp and conveys a sense of organization. I already have a logo.

Target Market(s)

Families (specifically mothers), small business owners, parents, seniors

Industry/Entity Type

Business

Contact Information for Business Card

My website is www.esnorganized-example.com and my Facebook page is http://www.sociallink-example.com/everyshelfsetneatly. The phone number is 418-552-7094 and I want to be listed as Lorna M. Pelham, Owner

Requirements
Must have
• My logo.

```html
<!DOCTYPE html>
<html lang="en">
<head>
<meta charset="utf-8">
<title>Every Shelf Set Neatly — Business Card</title>
<link rel="stylesheet" href="https://fonts.googleapis.com/css2?family=Montserrat:wght@500&family=Open+Sans:wght@400;600&display=swap">
<style>
  :root {
    --stage: #9b9b9b;
    --card-paper: #f3f3f3;
    --brand-blue: #1670c6;
    --ink: #2b2b2b;
    --ink-soft: #4a4a4a;
    --white: #ffffff;
  }
  * { box-sizing: border-box; margin: 0; padding: 0; }
  html, body {
    width: 1105px;
    height: 1200px;
    overflow: hidden;
    background: var(--stage);
  }
  .canvas {
    position: relative;
    width: 1105px;
    height: 1200px;
  }
  .card {
    position: absolute;
    left: 102px;
    width: 900px;
    height: 514px;
    overflow: hidden;
  }
  .card--front { top: 64px; background: var(--card-paper); }
  .card--back  { top: 622px; background: var(--brand-blue); }

  /* Front */
  .holder {
    position: absolute;
    right: 68px;
    top: 56px;
    text-align: right;
    font-family: "Open Sans", sans-serif;
  }
  .holder__name {
    font-size: 30px;
    font-weight: 600;
    color: var(--brand-blue);
    line-height: 1.1;
  }
  .holder__title {
    font-size: 21px;
    font-weight: 400;
    color: var(--ink);
    margin-top: 6px;
  }
  .accent-bar {
    position: absolute;
    right: 0;
    top: 60px;
    width: 23px;
    height: 67px;
    background: var(--brand-blue);
  }
  .wordmark {
    font-family: "Montserrat", sans-serif;
    font-weight: 500;
    letter-spacing: 3px;
    white-space: nowrap;
    display: flex;
    align-items: center;
    gap: 16px;
  }
  .wordmark__dot {
    width: 22px;
    height: 22px;
    border-radius: 50%;
  }
  .card--front .wordmark {
    position: absolute;
    left: 60px;
    top: 330px;
    font-size: 44px;
    color: var(--brand-blue);
  }
  .card--front .wordmark__dot { background: var(--brand-blue); }
  .divider {
    position: absolute;
    left: 60px;
    right: 60px;
    top: 403px;
    height: 2px;
    background: var(--brand-blue);
  }
  .contacts {
    position: absolute;
    left: 60px;
    right: 60px;
    top: 428px;
    display: flex;
    justify-content: space-between;
    align-items: center;
    list-style: none;
    font-family: "Open Sans", sans-serif;
    font-size: 22px;
    color: var(--ink-soft);
  }
  .contacts__item {
    display: flex;
    align-items: center;
    gap: 8px;
    white-space: nowrap;
  }
  .contacts__icon { width: 20px; height: 20px; flex: none; }
  .contacts__square {
    width: 18px;
    height: 18px;
    background: var(--brand-blue);
    flex: none;
  }

  /* Back */
  .card--back .wordmark {
    position: absolute;
    left: 0;
    right: 0;
    top: 78px;
    justify-content: center;
    font-size: 50px;
    color: var(--white);
  }
  .card--back .wordmark__dot { background: var(--white); }
  .back-url {
    position: absolute;
    left: 0;
    right: 0;
    top: 150px;
    text-align: center;
    font-family: "Open Sans", sans-serif;
    font-style: italic;
    font-size: 22px;
    letter-spacing: 6px;
    color: var(--white);
  }
</style>
</head>
<body>
<main class="canvas">
  <section class="card card--front" aria-label="Business card front">
    <div class="holder">
      <p class="holder__name">LORNA M. PELHAM</p>
      <p class="holder__title">OWNER</p>
    </div>
    <div class="accent-bar"></div>

    <div class="wordmark">
      <span class="wordmark__dot"></span>
      <span class="wordmark__name">ESN Organized</span>
    </div>

    <div class="divider"></div>

    <ul class="contacts">
      <li class="contacts__item">
        <svg class="contacts__icon" viewBox="0 0 24 24" aria-hidden="true">
          <path fill="#1670c6" d="M6.6 10.8a15.1 15.1 0 0 0 6.6 6.6l2.2-2.2a1 1 0 0 1 1-.25 11.4 11.4 0 0 0 3.6.57 1 1 0 0 1 1 1V20a1 1 0 0 1-1 1A17 17 0 0 1 3 4a1 1 0 0 1 1-1h3.5a1 1 0 0 1 1 1c0 1.25.2 2.45.57 3.57a1 1 0 0 1-.25 1z"/>
        </svg>
        <span>418-552-7094</span>
      </li>
      <li class="contacts__item">
        <svg class="contacts__icon" viewBox="0 0 24 24" aria-hidden="true">
          <circle cx="12" cy="12" r="10" fill="#1670c6"/>
          <path d="M2 12h20M12 2c3 3 3 17 0 20M12 2c-3 3-3 17 0 20" stroke="#f3f3f3" stroke-width="1.4" fill="none"/>
        </svg>
        <span>www.esnorganized-example.com</span>
      </li>
      <li class="contacts__item">
        <span class="contacts__square"></span>
        <span>everyshelfsetneatly</span>
      </li>
    </ul>
  </section>

  <section class="card card--back" aria-label="Business card back">
    <div class="wordmark">
      <span class="wordmark__dot"></span>
      <span class="wordmark__name">ESN Organized</span>
    </div>
    <p class="back-url">www.esnorganized-example.com</p>
  </section>
</main>
</body>
</html>
```